Business Card Design - Photographer

I am a landscape photographer and I require a business card design. 

I require two designs:
1)  a double sided business card
 and
b)  a single sided business card 

The single sided design can either be the same as the double sided (with just one side having all the information)....or it can be an entire new design. Its up to you.

My corporate colours are (CMYK):

Blue   69, 32, 0, 0
Grey  72,  64,  47,  31
Green  32,  2,  91,  0
Yellow   0, 19, 92, 0
Orange  0, 39, 75, 0

Colour space in final file should be in CMYK.

The details that need to be included on the card:

- Use the provided Logo
- Name: Wiktor Baranowski
- Email:   sales@vistalumeworks.com.au
- Website:    vistalumeworks.com.au
- Twitter:    twitter.com/vistalumeworks
- Facebook:   facebook.com/vistalumeworks
- Mobile  0417 539 662

Please use the attached template to design the logo to the specified size, including the marked bleed lines. I have also attached my logo in PNG (transparent background) and ai format for you to use.

The final file should be:
- Photoshop version with layers so I can edit the name/text etc. All non vector files should be high resolution at 1039 x 697 pixels at 300 dpi.

I also require a file as:
- Vector based PDF

Anyway questions please contact me.

Thank you

Industry/Entity Type

Landscape

Logo styles of interest
Pictorial/Combination Logo
Abstract Logo
Wordmark Logo
Lettermark Logo
Requirements
Must have
• The details that need to be included on the card:

- Use the provided Logo
- Name: Wiktor Baranowski
- Email: sales@vistalumeworks.com.au
- Website: vistalumeworks.com.au
- Twitter: twitter.com/vistalumeworks
- Facebook: facebook.com/vistalumeworks
- Mobile 0417 539 662

```html
<!DOCTYPE html>
<html lang="en">
<head>
<meta charset="utf-8">
<title>Business Card – Wiktor Baranowski</title>
<link rel="stylesheet" href="https://fonts.googleapis.com/css2?family=Cinzel:wght@500&family=Open+Sans:wght@400&family=Poiret+One&display=swap">
<style>
  :root {
    --backdrop: #3a2519;
    --paper: #f7f6f3;
    --ink: #1e1e1e;
    --grey: #5b5e66;
    --blue: #3b8fd0;
    --orange: #f3a33f;
    --green: #a8c639;
    --yellow: #fdcb1a;
  }
  * { box-sizing: border-box; margin: 0; padding: 0; }
  html, body { width: 1200px; height: 800px; overflow: hidden; }
  body {
    background: var(--backdrop);
    position: relative;
    font-family: "Open Sans", Arial, sans-serif;
  }
  .card {
    position: absolute;
    top: 216px;
    width: 563px;
    height: 367px;
    background: var(--paper);
    overflow: hidden;
  }
  .card--front { left: 33px; }
  .card--back { left: 603px; }

  .scatter {
    position: absolute;
    border-radius: 50%;
    opacity: .35;
  }
  .scatter--top { left: -40px; top: -40px; width: 220px; height: 180px;
    background: radial-gradient(closest-side, rgba(59,143,208,.35), rgba(243,163,63,.2), transparent); }
  .scatter--right { right: -40px; bottom: 10px; width: 240px; height: 220px;
    background: radial-gradient(closest-side, rgba(168,198,57,.3), rgba(253,203,26,.2), transparent); }

  .brand {
    position: absolute;
    left: 0; right: 0; top: 114px;
    text-align: center;
  }
  .brand__dot {
    display: block;
    width: 88px; height: 88px;
    margin: 0 auto 18px;
    border-radius: 50%;
    background: var(--ink);
  }
  .brand__name {
    font-family: "Cinzel", Georgia, serif;
    font-weight: 500;
    font-size: 25px;
    letter-spacing: .5px;
    color: var(--ink);
  }

  .web-rule {
    position: absolute;
    left: 0; right: 0; top: 337px;
    height: 1.5px;
    background: var(--orange);
  }
  .web-rule__text {
    position: absolute;
    left: 50%; top: -9px;
    transform: translateX(-50%);
    background: var(--paper);
    padding: 0 6px;
    font-size: 14px;
    line-height: 18px;
    color: var(--orange);
    white-space: nowrap;
  }
  .card--front .web-rule__text { left: 281px; }

  .frame { position: absolute; left: 0; top: 0; }

  .person {
    position: absolute;
    left: 0; right: 0; top: 134px;
    text-align: center;
  }
  .person__name {
    font-family: "Poiret One", sans-serif;
    font-size: 44px;
    line-height: 48px;
    color: var(--ink);
  }
  .person__role {
    font-size: 13px;
    color: var(--grey);
    margin-top: 0;
  }

  .contact {
    position: absolute;
    list-style: none;
    font-size: 12.5px;
    line-height: 18px;
    color: var(--grey);
  }
  .contact li { display: flex; align-items: center; gap: 6px; white-space: nowrap; }
  .contact--direct { left: 103px; top: 276px; }
  .contact--social { left: 337px; top: 276px; }
  .contact__icon { width: 13px; height: 13px; flex: none; }
  .contact__square { width: 13px; height: 13px; border-radius: 2px; background: var(--grey); flex: none; }
</style>
</head>
<body>

<section class="card card--front" aria-label="Card front">
  <div class="scatter scatter--top" role="img" aria-label="Scattered coloured leaves"></div>
  <div class="scatter scatter--right" role="img" aria-label="Scattered coloured leaves"></div>
  <div class="brand">
    <span class="brand__dot"></span>
    <p class="brand__name">VISTALUME WORKS</p>
  </div>
  <div class="web-rule"><span class="web-rule__text">www.vistalumeworks.com.au</span></div>
</section>

<section class="card card--back" aria-label="Card back">
  <div class="scatter scatter--top" role="img" aria-label="Scattered coloured leaves"></div>
  <div class="scatter scatter--right" role="img" aria-label="Scattered coloured leaves"></div>

  <svg class="frame" width="563" height="367" aria-hidden="true">
    <g fill="none" stroke="var(--blue)" stroke-width="3.5">
      <path d="M55 89 V74 H69"/>
      <path d="M494 74 H508 V89"/>
      <path d="M55 238 V253 H69"/>
      <path d="M494 253 H508 V238"/>
    </g>
  </svg>

  <div class="person">
    <h1 class="person__name">Wiktor Baranowski</h1>
    <p class="person__role">photographer</p>
  </div>

  <ul class="contact contact--direct">
    <li>
      <svg class="contact__icon" viewBox="0 0 13 13" aria-hidden="true"><rect x="3" y="0.5" width="7" height="12" rx="1.2" fill="none" stroke="var(--grey)" stroke-width="1.2"/><rect x="4.3" y="2" width="4.4" height="7" fill="var(--grey)"/></svg>
      <span>0417 539 662</span>
    </li>
    <li>
      <svg class="contact__icon" viewBox="0 0 13 13" aria-hidden="true"><rect x="0.5" y="3" width="12" height="8" fill="var(--grey)"/><path d="M0.5 3 L6.5 8 L12.5 3" fill="none" stroke="var(--paper)" stroke-width="1"/></svg>
      <span>sales@vistalumeworks.com.au</span>
    </li>
  </ul>

  <ul class="contact contact--social">
    <li><span class="contact__square"></span><span>vistalumeworks</span></li>
    <li><span class="contact__square"></span><span>vistalumeworks</span></li>
  </ul>

  <div class="web-rule"><span class="web-rule__text">www.vistalumeworks.com.au</span></div>
</section>

</body>
</html>
```